Website for my photography business

I need a website for my photography business, Bram Kellet Photography. I need a website that has a landing page with a cover photo of each kind of photography I do. For example, Nature, Weddings, Portraits and Architecture. I want it so that when someone comes onto my website they have to choose which kind of photography page they want to visit. So if they click on the wedding photo it will open to a page with my wedding portfolio images and a contact me button. If they choose nature photography I want them to be redirected to an e-commerce section where they can purchase prints. Architecture and Portraits should open up to their respective portfolios with about me and contact info. I like this kind of format because I want people who come to my website for a specific type of photography to be able to be directed there easily without having to look at a mix of other kinds of photography. I will provide a few files to use as placeholders. I have already purchased the bramkelletphotography.example domain name. A Wix website would be great because I am most familiar with it but I am open to anything.

Industry/Entity Type

Photographer

Number of Pages Required

5+ page

Requirements
Must have
• Landing Page and e-commerce

```html
<!DOCTYPE html>
<html lang="en">
<head>
<meta charset="utf-8">
<title>Bram Kellet Photography</title>
<link href="https://fonts.googleapis.com/css2?family=IBM+Plex+Sans:wght@400;500&family=Inter:wght@400;500&display=swap" rel="stylesheet">
<style>
  :root {
    --ink: #111111;
    --rule: #8a8a8a;
    --paper: #ffffff;
    --accent: #f6b42a;
    --brand: #1d2454;
  }
  * { margin: 0; padding: 0; box-sizing: border-box; }
  html, body { width: 883px; height: 1200px; overflow: hidden; background: var(--paper); }
  .site {
    position: relative; width: 883px; height: 1200px;
    color: var(--ink); font-family: "Inter", Arial, sans-serif;
  }
  .brand {
    position: absolute; left: 20px; top: 34px;
    display: flex; align-items: center; gap: 8px;
    font-family: "IBM Plex Sans", sans-serif; font-weight: 400;
    font-size: 21px; color: var(--brand); letter-spacing: 0.2px;
  }
  .brand-dot { width: 8px; height: 8px; border-radius: 50%; background: var(--accent); }
  .menu-toggle { position: absolute; left: 841px; top: 8px; width: 34px; height: 30px; }
  .contact-links { position: absolute; top: 96px; left: 20px; font-size: 11.5px; line-height: 17px; }
  .contact-links span { position: absolute; white-space: nowrap; }
  .contact-links .email { font-weight: 500; font-size: 9.5px; }
  .rule-h { position: absolute; left: 20px; width: 850px; height: 1px; background: var(--rule); }
  .rule-v { position: absolute; left: 439px; top: 152px; width: 1px; height: 965px; background: var(--rule); }
  .category-photo { position: absolute; width: 382px; height: 309px; }
  .open-btn {
    position: absolute; width: 19px; height: 20px; background: var(--accent);
    display: flex; align-items: center; justify-content: center;
    font: 500 13px/1 "Inter", sans-serif; color: var(--ink);
  }
  .category-title {
    position: absolute; font-family: "IBM Plex Sans", sans-serif;
    font-weight: 400; font-size: 34px; line-height: 1; white-space: nowrap;
  }
  .category-title.vertical { transform-origin: left top; transform: rotate(90deg); }
  .photo-nature { left: 25px; top: 177px; background: linear-gradient(180deg, #1f3a2c 0%, #2d4a35 35%, #b86b2c 55%, #e9edf2 70%, #f5f7fa 100%); }
  .photo-wedding { left: 472px; top: 232px; background: radial-gradient(circle at 60% 50%, #2a3347 0%, #6e6157 30%, #a58767 65%, #8d7a69 100%); }
  .photo-architecture { left: 25px; top: 627px; background: linear-gradient(180deg, #d8dadc 0%, #9d5a45 35%, #b7a99a 60%, #a9a7a2 85%, #6c9a45 100%); }
  .photo-portrait { left: 472px; top: 765px; background: linear-gradient(135deg, #3a3a3a 0%, #9a9a9a 40%, #6d6d6d 70%, #2a2a2a 100%); }
  .footer-note { position: absolute; left: 20px; top: 1160px; font-family: "IBM Plex Sans", sans-serif; font-size: 10.5px; }
</style>
</head>
<body>
<div class="site">
  <header>
    <div class="brand"><span class="brand-dot"></span>Bram Kellet Photography</div>
    <svg class="menu-toggle" viewBox="0 0 34 30" aria-label="Menu">
      <rect x="0" y="0" width="34" height="2.8" fill="#111"/>
      <rect x="9" y="13.6" width="25" height="2.8" fill="#111"/>
      <rect x="0" y="27.2" width="34" height="2.8" fill="#111"/>
    </svg>
    <div class="contact-links">
      <span style="left:0;top:0">Photobook</span>
      <span style="left:0;top:17px">Snapgram</span>
      <span style="left:75px;top:0">Pinboard</span>
      <span style="left:75px;top:17px">Linkworks</span>
      <span class="email" style="left:144px;top:1px">info@bramkelletphotography.example</span>
      <span style="left:143px;top:17px">555-014-2290</span>
    </div>
  </header>

  <div class="rule-h" style="top:152px"></div>
  <div class="rule-v"></div>
  <div class="rule-h" style="top:578px"></div>

  <a class="category">
    <div class="category-photo photo-nature" role="img" aria-label="Red fox sitting on snow in front of pine trees"></div>
    <span class="open-btn" style="left:387px;top:177px">+</span>
    <h2 class="category-title" style="left:22px;top:500px">Nature</h2>
  </a>

  <a class="category">
    <h2 class="category-title" style="left:470px;top:174px">Weddings</h2>
    <div class="category-photo photo-wedding" role="img" aria-label="Two wedding rings resting on granite rock"></div>
    <span class="open-btn" style="left:835px;top:233px">+</span>
  </a>

  <a class="category">
    <div class="category-photo photo-architecture" role="img" aria-label="Brick and stone campus building with a patrol car in front"></div>
    <span class="open-btn" style="left:387px;top:628px">+</span>
    <h2 class="category-title" style="left:22px;top:957px">Architecture</h2>
  </a>

  <a class="category">
    <h2 class="category-title vertical" style="left:506px;top:623px">Portraits</h2>
    <span class="open-btn" style="left:835px;top:683px">+</span>
    <div class="category-photo photo-portrait" role="img" aria-label="Black and white study of folded arms and shoulders"></div>
  </a>

  <div class="rule-h" style="top:1140px"></div>
  <footer class="footer-note">Copyright © 2020 All Rights Reserved</footer>
</div>
</body>
</html>
```